BRELWINCare.co.uk - Mental Health Clinic for Child and Adolescents

Updated 29/01/2018***
I am not sure you guys are getting the idea regards to the opening page / homescreen layout. Can you look at the new images I have uploaded (page 5, 6 and 7) These are some of the layouts I like but to incorporate my chosen images, with the BRELWIN commissioner, buttons and a sliding header bar.
I have written a strong brief, I am looking for a website, preferably wordpress as i know they are easy to maintain. I am looking for a one page site, with the top / opening page being full screen image with drop down categories. I have made a rough design, see full brief in word doc attached, there is some freedom to play around with the design aspect but it will need to relay all the content provided. I like a minimal feel. I have also attached some images that may be useful, but will need a new logo for BRELWIN Care. I have attached some logo idea's, it is up to you decide whether you want to use them.
I would prefer the homepage as full screen image, and the categories offered as a drop down or over the main image.
I have also attached linked to some competitors websites:
https://www.vorimant-health.co.uk/
http://www.qlbn.org.uk/
Industry/Entity Type
Clinic
Number of Pages Required
1 page
Font styles to use
Look and feel
Each slider illustrates characteristics of the customer's brand and the style your logo design should communicate.

```html
<!DOCTYPE html>
<html lang="en">
<head>
<meta charset="utf-8">
<title>BRELWIN Care – Child &amp; Adolescent Mental Health</title>
<link rel="stylesheet" href="https://fonts.googleapis.com/css2?family=Lato:wght@400;700&display=swap">
<style>
:root{
  --yellow:#f7ec0f;
  --magenta:#e5097f;
  --purple:#7b2a84;
  --green:#9bc53d;
  --teal:#29bccf;
  --blue-deep:#23509c;
  --blue-light:#05b1cb;
  --ink:#111;
  --grey-text:#666;
  --heading-grey:#4b4b4b;
  --white:#fff;
}
*{box-sizing:border-box;margin:0;padding:0}
html,body{width:1200px;height:2344px;overflow:hidden;background:var(--white)}
body{font-family:'Lato',sans-serif;position:relative;color:var(--ink)}
.abs{position:absolute}

/* Header */
.sidebar{left:0;top:0;width:358px;height:659px;background:var(--white)}
.sidebar-curve{left:0;top:150px;width:358px;height:509px}
.brand{left:40px;top:58px;display:flex;align-items:center;gap:14px}
.brand-dot{width:58px;height:58px;border-radius:50%;background:var(--yellow)}
.brand-name{font-weight:700;font-size:36px;color:var(--purple);letter-spacing:1px}
.main-nav{left:59px;top:240px;width:266px;list-style:none}
.main-nav li{height:45px;border-bottom:1px solid #8a8420;display:flex;align-items:center;justify-content:center;font-weight:700;font-size:20px;color:var(--ink)}
.main-nav li:last-child{border-bottom:none}

.hero{left:358px;top:0;width:842px;height:659px;background:linear-gradient(135deg,#e9e6e1 0%,#cfc3b4 45%,#8d7a66 100%)}
.audience{top:388px;height:97px;width:297px;border-radius:50%;display:flex;align-items:center;justify-content:center;color:var(--white);font-size:24px;font-weight:400;letter-spacing:.3px}
.audience::after{content:"";position:absolute;inset:8px;border:2px solid var(--white);border-radius:50%}
.audience-parents{left:440px;background:var(--purple)}
.audience-commissioners{left:763px;background:var(--green)}
.hero-banner{left:358px;top:581px;width:842px;height:78px;background:var(--teal);opacity:.92;display:flex;align-items:center;padding-left:37px;color:var(--white);font-weight:700;font-size:23px}
.hero-arrows{right:88px;top:603px;display:flex;gap:22px}

/* Welcome */
.welcome{left:159px;top:725px;width:886px;height:272px;border:2px solid var(--magenta);border-radius:62px}
.welcome-mark{left:572px;top:693px;width:62px;height:62px;background:var(--white);display:flex;align-items:center;justify-content:center}
.welcome-mark span{width:44px;height:44px;border-radius:50%;background:var(--yellow)}
.welcome h1{position:absolute;left:0;right:0;top:50px;text-align:center;font-size:32px;font-weight:700;color:var(--heading-grey)}
.welcome h1 em{font-style:normal;color:var(--teal)}
.welcome p{position:absolute;left:60px;right:60px;top:105px;text-align:center;font-size:18.5px;line-height:31px;color:var(--grey-text)}
.btn-solid{left:518px;top:969px;width:172px;height:47px;border-radius:24px;background:var(--magenta);color:var(--white);font-weight:700;font-size:17px;display:flex;align-items:center;justify-content:center}

/* Blogs */
.blogs{left:0;top:1080px;width:1200px;height:509px;background:linear-gradient(120deg,var(--blue-deep) 0%,#1575b4 50%,var(--blue-light) 100%)}
.blogs h2{position:absolute;left:0;right:0;top:46px;text-align:center;color:var(--white);font-size:31px;font-weight:700}
.blog-card{top:104px;width:300px;text-align:center;color:var(--white)}
.blog-photo{margin:0 auto;width:200px;height:200px;border-radius:50%;border:5px solid var(--yellow);padding:8px}
.blog-photo div{width:100%;height:100%;border-radius:50%}
.blog-card h3{margin-top:20px;font-size:20px;font-weight:700}
.blog-card p{margin-top:6px;font-size:14.5px;line-height:23px;padding:0 8px}
.btn-outline{margin:18px auto 0;width:153px;height:45px;border:2px solid var(--white);border-radius:23px;display:flex;align-items:center;justify-content:center;font-weight:700;font-size:16px}
.blog-arrow{top:253px}

/* Contact */
.contact{left:0;top:1589px;width:1200px;height:549px;background:linear-gradient(180deg,#f1f1f0 0%,#e6e6e4 55%,#d2cfca 100%)}
.contact-frame{left:273px;top:1661px;width:660px;height:260px;border:2px solid var(--magenta);border-bottom:none;border-radius:40px 40px 0 0}
.contact h2{position:absolute;left:495px;top:1640px;width:216px;background:#efefee;text-align:center;color:var(--magenta);font-size:31px;font-weight:700}
.contact-details{left:273px;top:1698px;width:660px;text-align:center;font-size:18px;line-height:31px;color:#333;list-style:none}
.group-photo{left:138px;top:1836px;width:893px;height:302px;background:linear-gradient(90deg,#5d6f86 0%,#c59a7a 35%,#d8b97a 55%,#6d5e5a 75%,#7b7f9b 100%);border-radius:60px 60px 0 0}

/* Footer */
.footer{left:0;top:2138px;width:1200px;height:206px;background:var(--purple);color:var(--white)}
.footer-nav{position:absolute;left:0;right:0;top:38px;display:flex;justify-content:center;gap:18px;list-style:none;font-weight:700;font-size:17px}
.footer-copy{position:absolute;left:0;right:0;top:77px;text-align:center;font-size:15px}
.social{position:absolute;left:505px;top:123px;display:flex;gap:6px}
.social span{width:44px;height:44px;border:2px solid var(--white);border-radius:50%}
</style>
</head>
<body>

<header>
  <div class="abs sidebar"></div>
  <svg class="abs sidebar-curve" viewBox="0 0 358 509" aria-hidden="true">
    <path d="M0 62 Q179 -10 358 62 L358 509 L0 509 Z" fill="#f7ec0f"/>
    <path d="M0 62 Q179 -10 358 62" fill="none" stroke="#e5097f" stroke-width="5"/>
  </svg>
  <div class="abs brand"><span class="brand-dot"></span><span class="brand-name">BRELWIN</span></div>
  <ul class="abs main-nav">
    <li>ABOUT US</li><li>OUR TEAM</li><li>OUR SERVICES</li><li>BLOGS</li>
    <li>FORUM</li><li>CONTACT US</li><li>PARENTS</li><li>COMMISIONERS</li>
  </ul>

  <div class="abs hero" role="img" aria-label="Photo of a therapist talking with a young person in a bright room"></div>
  <div class="abs audience audience-parents">PARENTS</div>
  <div class="abs audience audience-commissioners">COMMISIONERS</div>
  <div class="abs hero-banner">ADHD and Austim Screening with 24 Hours</div>
  <div class="abs hero-arrows" aria-hidden="true">
    <svg width="22" height="36" viewBox="0 0 22 36"><path d="M18 3 L4 18 L18 33" fill="none" stroke="#fff" stroke-width="4"/></svg>
    <svg width="22" height="36" viewBox="0 0 22 36"><path d="M4 3 L18 18 L4 33" fill="none" stroke="#fff" stroke-width="4"/></svg>
  </div>
</header>

<section class="abs welcome">
  <h1>WELCOME TO <em>BRELWIN</em></h1>
  <p>Vivamus porttitor purus nisi eleifend libero a tempus libero lectus feugiat felis Morbi diam mauris viverra in gravida eu mattis in ante Morbi eget arcu Morbi porta libero id ullamcorper nonummy nibh ligula pulvinar metus eget consectetuer augue nisi quis lacus Ut</p>
</section>
<div class="abs welcome-mark" aria-hidden="true"><span></span></div>
<div class="abs btn-solid">READ MORE</div>

<section class="abs blogs">
  <h2>OUR BLOGS</h2>
  <svg class="abs blog-arrow" style="left:122px" width="24" height="40" viewBox="0 0 24 40" aria-hidden="true"><path d="M20 3 L5 20 L20 37" fill="none" stroke="#fff" stroke-width="4"/></svg>
  <svg class="abs blog-arrow" style="left:1070px" width="24" height="40" viewBox="0 0 24 40" aria-hidden="true"><path d="M4 3 L19 20 L4 37" fill="none" stroke="#fff" stroke-width="4"/></svg>

  <article class="abs blog-card" style="left:141px">
    <div class="blog-photo"><div role="img" aria-label="Photo of a girl sitting at home" style="background:linear-gradient(135deg,#e8e4df,#a98c76)"></div></div>
    <h3>Aorta libero ullamcorper</h3>
    <p>nonummy nibh ligula pulvinar metus eget consectetuer augue nisi quis</p>
    <div class="btn-outline">READ MORE</div>
  </article>
  <article class="abs blog-card" style="left:455px">
    <div class="blog-photo"><div role="img" aria-label="Photo of a woman in conversation on a sofa" style="background:linear-gradient(135deg,#c9c7c4,#4d6589)"></div></div>
    <h3>Fusce ultricies orci</h3>
    <p>nonummy nibh ligula pulvinar metus eget consectetuer augue nisi quis</p>
    <div class="btn-outline">READ MORE</div>
  </article>
  <article class="abs blog-card" style="left:770px">
    <div class="blog-photo"><div role="img" aria-label="Photo of a teenage boy sitting in a room" style="background:linear-gradient(135deg,#b9b4ad,#5e3a36)"></div></div>
    <h3>Nulla rhoncus dictu</h3>
    <p>nonummy nibh ligula pulvinar metus eget consectetuer augue nisi quis</p>
    <div class="btn-outline">READ MORE</div>
  </article>
</section>

<section>
  <div class="abs contact" role="img" aria-label="Photo of a white brick wall"></div>
  <div class="abs contact-frame"></div>
  <div class="contact"><h2>CONTACT US</h2></div>
  <ul class="abs contact-details">
    <li>Phone Number: 0203 555 0148</li>
    <li>Address:&nbsp; Larkfield Suite 2B, 41-47 Mill Lane, London, E9 4TR</li>
    <li>Opening Times: 9am – 5pm Mon-Fri</li>
    <li>Email: enquiry@brelwincare.co.uk</li>
  </ul>
  <div class="abs group-photo" role="img" aria-label="Photo of five smiling teenagers sitting together on a sofa"></div>
</section>

<footer class="abs footer">
  <ul class="footer-nav">
    <li>ABOUT US</li><li>OUR TEAM</li><li>OUR SERVICES</li><li>BLOGS</li>
    <li>CONTACT US</li><li>PARENTS</li><li>COMMISIONERS</li>
  </ul>
  <p class="footer-copy">© 2018 Company Name&nbsp; All right reserved</p>
  <div class="social" aria-label="Social links"><span></span><span></span><span></span><span></span></div>
</footer>

</body>
</html>
```